Disposable Mini Sauce Pot Design for Asian Chain Food Brands

We operate a Hainan Chicken Rice takeout brand under the name Brindle4U, with our official website: www.Brindle4U.example.
We offer four signature house sauces and are launching brand-new packaging for our sauce line. We require custom graphic designs exclusively for the sauce cup lids.
Product Material & Base Specs
The sauce cups are made of PP plastic, available in two translucent base options: Translucent White and Translucent Orange.
Four Sauce Varieties for Individual Lid Designs
1. Red Sauce – Fried Sweet Chili Sauce
2.Green Sauce – Scallion Oil Dressing
3.Sweet Soy Sauce
4.Sweet Red Sauce (Special for Fried Chicken)
Differentiate each sauce lid design through unique graphics, typography, or illustrative elements for easy customer identification.
The marking NET WT 2 OZ must be clearly printed on every lid.
**There is no need to print full descriptive text or the full name of the sauces on each lid; the design only needs to clearly differentiate the four sauce varieties.
**Please reference the original design style and brand color palette shown on our official website, and feel free to fully unleash your creativity.
Look and feel
Each slider illustrates characteristics of the customer's brand and the style your logo design should communicate.

```html
<!DOCTYPE html>
<html lang="en">
<head>
<meta charset="utf-8">
<title>Brindle4U Sauce Lid Labels</title>
<link href="https://fonts.googleapis.com/css2?family=Montserrat:wght@500;700;800&display=swap" rel="stylesheet">
<style>
  :root {
    --page-bg: #ffffff;
    --ink-white: #ffffff;
    --size-note: #3a3a3a;

    --red-title: #a5151b;
    --red-fill: #b30b10;
    --red-rule: #f5221f;

    --green-title: #426619;
    --green-fill: #3b6612;
    --green-rule: #6c9c22;

    --soy-title: #4a3226;
    --soy-fill: #3b2117;
    --soy-rule: #9c4f1c;
    --soy-accent: #ec6d2e;
    --soy-drop: #eaa54a;

    --sweet-title: #d9430f;
    --sweet-fill: #e8692a;
    --sweet-rule: #ff9c12;
    --sweet-star: #d6e21c;
  }
  * { margin: 0; padding: 0; box-sizing: border-box; }
  html, body { width: 1109px; height: 1200px; overflow: hidden; background: var(--page-bg); }
  body { position: relative; font-family: "Montserrat", Arial, sans-serif; }

  .variant-title {
    position: absolute; width: 351px; text-align: center;
    font-weight: 800; font-size: 20px; letter-spacing: 0.2px;
  }
  .lid-label {
    position: absolute; width: 351px; height: 398px;
    border-radius: 54px; color: var(--ink-white); text-align: center;
  }
  .lid-label::before {
    content: ""; position: absolute; inset: 10px;
    border: 1.5px solid var(--rule); border-radius: 45px;
  }
  .sauce-name {
    position: absolute; top: 36px; left: 0; right: 0;
    font-weight: 500; font-size: 18px; letter-spacing: 3.5px;
  }
  .brand-name {
    position: absolute; top: 86px; left: 0; right: 0;
    font-weight: 800; font-size: 62px; line-height: 74px; letter-spacing: -1px;
    color: var(--brand, var(--ink-white));
  }
  .dish-name {
    position: absolute; top: 252px; left: 0; right: 0;
    font-weight: 800; font-size: 22px; letter-spacing: 1.5px;
    color: var(--brand, var(--ink-white));
  }
  .sauce-icon { position: absolute; top: 311px; left: 163px; width: 26px; height: 30px; }
  .net-weight {
    position: absolute; top: 347px; left: 0; right: 0;
    font-weight: 800; font-size: 22px;
  }
  .size-note {
    position: absolute; top: 1153px; left: 0; width: 1109px; text-align: center;
    font-weight: 500; font-size: 18px; color: var(--size-note);
  }

  .lid-red { left: 136px; top: 150px; background: var(--red-fill); --rule: var(--red-rule); }
  .lid-green { left: 617px; top: 150px; background: var(--green-fill); --rule: var(--green-rule); }
  .lid-soy { left: 136px; top: 685px; background: var(--soy-fill); --rule: var(--soy-rule); --brand: var(--soy-accent); }
  .lid-sweet { left: 617px; top: 685px; background: var(--sweet-fill); --rule: var(--sweet-rule); }
</style>
</head>
<body>
  <h2 class="variant-title" style="left:136px; top:92px; color:var(--red-title);">RED SAUCE</h2>
  <h2 class="variant-title" style="left:617px; top:92px; color:var(--green-title);">GREEN SAUCE</h2>
  <h2 class="variant-title" style="left:136px; top:630px; color:var(--soy-title);">SWEET SOY SAUCE</h2>
  <h2 class="variant-title" style="left:617px; top:632px; color:var(--sweet-title);">SWEET RED SAUCE</h2>

  <section class="lid-label lid-red">
    <p class="sauce-name">RED SAUCE</p>
    <p class="brand-name">Brindle<br>4U</p>
    <p class="dish-name">HAINAN CHICKEN</p>
    <svg class="sauce-icon" viewBox="0 0 26 30" aria-label="flame">
      <path d="M13 1C15 7 22 10 22 19a9 9 0 0 1-18 0c0-5 3-7 4-10 1 3 2 4 3 5 1-5 2-9 2-13z" fill="#fff"/>
      <path d="M13 16c2 3 4 4 4 7a4 4 0 0 1-8 0c0-3 3-4 4-7z" fill="var(--red-fill)"/>
    </svg>
    <p class="net-weight">NET WT 2 OZ</p>
  </section>

  <section class="lid-label lid-green">
    <p class="sauce-name">GREEN SAUCE</p>
    <p class="brand-name">Brindle<br>4U</p>
    <p class="dish-name">HAINAN CHICKEN</p>
    <svg class="sauce-icon" viewBox="0 0 26 30" aria-label="leaf">
      <path d="M7 22C4 12 12 6 23 7c0 11-6 18-16 15z" fill="#fff"/>
      <path d="M3 27L12 16" stroke="#fff" stroke-width="1.6" fill="none"/>
    </svg>
    <p class="net-weight">NET WT 2 OZ</p>
  </section>

  <section class="lid-label lid-soy">
    <p class="sauce-name">SWEET SOY SAUCE</p>
    <p class="brand-name">Brindle<br>4U</p>
    <p class="dish-name">HAINAN CHICKEN</p>
    <svg class="sauce-icon" viewBox="0 0 26 30" aria-label="drop">
      <path d="M13 4C17 11 21 15 21 20a8 8 0 0 1-16 0c0-5 4-9 8-16z" fill="var(--soy-drop)"/>
    </svg>
    <p class="net-weight">NET WT 2 OZ</p>
  </section>

  <section class="lid-label lid-sweet">
    <p class="sauce-name">SWEET RED SAUCE</p>
    <p class="brand-name">Brindle<br>4U</p>
    <p class="dish-name">HAINAN CHICKEN</p>
    <svg class="sauce-icon" viewBox="0 0 26 30" aria-label="star">
      <path d="M13 5l2.6 6.2 6.7.5-5.1 4.3 1.6 6.5L13 19l-5.8 3.5 1.6-6.5-5.1-4.3 6.7-.5z" fill="var(--sweet-star)"/>
    </svg>
    <p class="net-weight">NET WT 2 OZ</p>
  </section>

  <p class="size-note">SIZE : 57.50 MM (W) X 65 MM (H)__9 MM CORNER REDIOUS</p>
</body>
</html>
```